New Innovative Counselling and psychotherapy Service needs Business Card design

Keep it simple and professional. On one side, just company name and logo (perhaps in all blue) and maybe a tag line.

On other side (all white) my name and Qualifications in centre

Industry/Entity Type

Health And Wellness

Contact Information for Business Card

Dara Whelby
Counsellor & Psychotherapist
BSc (Psychol.), BA, Dip. (Couns. & Psych.), PG.Cert (CBT), FGTrK, ONRE

I will also require Mobile no, Email and web site address of which I'll pass on to final designer.

Font styles to use
Sans Serif

Requirements
Must have
• My Logo Only and please use the colours in logo that is in it.
Should not have
• Any other images

```html
<!DOCTYPE html>
<html lang="en">
<head>
<meta charset="utf-8">
<title>Brightwell Path – Business Card</title>
<link rel="stylesheet" href="https://fonts.googleapis.com/css2?family=Montserrat:wght@300;400&family=Roboto:wght@400;700&display=swap">
<style>
  :root {
    --page: #e9eaec;
    --card-white: #f7f7f7;
    --brand-blue: #45a6df;
    --brand-green: #86c24f;
    --grad-blue: #5dbde8;
    --grad-green: #9bd36b;
    --ink: #2f3134;
    --white: #ffffff;
  }
  * { margin: 0; padding: 0; box-sizing: border-box; }
  html, body { width: 1200px; height: 726px; overflow: hidden; }
  body {
    background: var(--page);
    font-family: "Roboto", Arial, sans-serif;
    position: relative;
  }
  .card {
    position: absolute;
    top: 208px;
    width: 540px;
    height: 309px;
    border-radius: 4px;
    overflow: hidden;
    box-shadow: 0 6px 18px rgba(0,0,0,0.12);
  }
  /* Front side */
  .card-front {
    left: 40px;
    background: linear-gradient(120deg, var(--grad-blue) 0%, #7ecbc0 50%, var(--grad-green) 100%);
  }
  .front-decoration {
    position: absolute; inset: 0;
    background: radial-gradient(circle at 45% 45%, rgba(255,255,255,0.10), rgba(255,255,255,0) 60%);
  }
  .front-wordmark {
    position: absolute;
    left: 0; right: 0; top: 128px;
    text-align: center;
    font-family: "Montserrat", Arial, sans-serif;
    font-weight: 300;
    font-size: 44px;
    letter-spacing: 1px;
    color: var(--white);
  }
  /* Back side */
  .card-back {
    left: 620px;
    background: var(--card-white);
  }
  .back-waves { position: absolute; inset: 0; width: 540px; height: 309px; }
  .holder {
    position: absolute;
    right: 22px; top: 14px;
    text-align: right;
    color: var(--white);
  }
  .holder-name { font-weight: 700; font-size: 19px; line-height: 1.1; margin-bottom: 2px; }
  .holder-role, .holder-quals { font-size: 10.5px; line-height: 1.3; }
  .contact {
    position: absolute;
    right: 22px; top: 172px;
    list-style: none;
    text-align: right;
    font-size: 13.5px;
    line-height: 1.5;
    color: var(--ink);
  }
  .contact li { display: flex; justify-content: flex-end; align-items: center; gap: 6px; }
  .contact svg { width: 12px; height: 12px; }
  .brand-mark {
    position: absolute;
    left: 60px; top: 194px;
    width: 56px; height: 56px;
    border-radius: 50%;
    background: var(--brand-blue);
  }
  .brand-name {
    position: absolute;
    left: 30px; top: 254px;
    font-family: "Montserrat", Arial, sans-serif;
    font-weight: 400;
    font-size: 30px;
    line-height: 1.2;
    color: var(--ink);
  }
</style>
</head>
<body>

  <section class="card card-front" aria-label="Business card front">
    <div class="front-decoration" role="img" aria-label="Soft blue-to-green brand backdrop"></div>
    <p class="front-wordmark">Brightwell Path</p>
  </section>

  <section class="card card-back" aria-label="Business card back">
    <svg class="back-waves" viewBox="0 0 540 309" aria-hidden="true">
      <path d="M0 0 H540 V108 C490 118 450 150 370 152 C270 154 150 140 0 168 Z" fill="var(--brand-blue)"/>
      <path d="M0 180 C140 150 250 160 370 160 C450 160 495 130 540 118" fill="none" stroke="var(--brand-green)" stroke-width="5"/>
      <path d="M40 188 C140 160 240 162 330 164" fill="none" stroke="var(--brand-green)" stroke-width="3"/>
    </svg>

    <div class="holder">
      <p class="holder-name">Dara Whelby</p>
      <p class="holder-role">Counsellor &amp; Psychotherapist</p>
      <p class="holder-quals">BSc (Psychol.), BA, Dip. (Couns.<br>&amp; Psych.), PG.Cert (CBT),<br>FGTrK, ONRE</p>
    </div>

    <ul class="contact">
      <li>0987 654 3210
        <svg viewBox="0 0 12 12"><path d="M2 1 L4 1 L5 3.5 L3.8 4.5 C4.5 6 6 7.5 7.5 8.2 L8.5 7 L11 8 L11 10 C11 10.6 10.6 11 10 11 C5 11 1 7 1 2 C1 1.4 1.4 1 2 1 Z" fill="var(--brand-blue)"/></svg>
      </li>
      <li>dara.w@BrightwellPath.com
        <svg viewBox="0 0 12 12"><rect x="1" y="2.5" width="10" height="7" fill="var(--brand-green)"/><path d="M1 2.5 L6 6.5 L11 2.5" fill="none" stroke="var(--white)" stroke-width="1"/></svg>
      </li>
      <li>www.BrightwellPath.com
        <svg viewBox="0 0 12 12"><circle cx="6" cy="6" r="5" fill="var(--brand-blue)"/><path d="M1 6 H11 M6 1 C3.5 3.5 3.5 8.5 6 11 M6 1 C8.5 3.5 8.5 8.5 6 11" fill="none" stroke="var(--white)" stroke-width="0.7"/></svg>
      </li>
    </ul>

    <div class="brand-mark" aria-hidden="true"></div>
    <p class="brand-name">Brightwell Path</p>
  </section>

</body>
</html>
```